Business Card: RW Office Partners - Your organised problem solver

Business Name: RW Office Partners
Website: www.rwofficepartners.com.au
Email: marisol@rwofficepartners.com.au
Mobile: 61 482 907 236
Facebook: @rwofficepartners
Instrgram: @rwofficepartners

Brading Colours:
HEX
#986474
#ddccd3
#7a8498
#c9d8e4
#000000
#ffffff

Tag Line: Your organised problem solver

Link to DRAFT website:
https://deskhelpcollective.wixsite.com/rw-office-partners

About Page from the website:
My name is Marisol Wrenfield, and I would love to assist you to become more productive in your day to day and achieve your business and personal goals.
My mission is to give you time, time to work on the important tasks of your business or to be able to spend more time with your family. I will take on the tasks you don’t have time for, don’t know well or simply don’t like to do.
I have an extensive background in Administration, Tender Coordination, Document Control, WHS and Quality Management working primarily in the Construction, Mining and Corporate World.
I am passionate about being organised, having order and making things in your life (and mine) easier! I love to watch something unfold and grow into something amazing! I am known for being the go-to problem solver, the organiser of all things, producing high standards of work even under pressure. I’m also a confident communicator, and I understand that you’re busy running your business.

Target Market(s)

Small to Medium Business who require assistance in their business by a virtual assistant.

Industry/Entity Type

Virtual Assistant

Contact Information for Business Card

Mobile: 61 482 907 236

Font styles to use
Sans Serif

Colors
ffffff

Requirements
Must have
• Branding Colours as outlined.
Contact Details as outlined.
Logo as provided.
Proper contact details - mobile, facebook, instragm, website.
Simple, Elegant, very clean looking.
Should not have
• Note cute with pictures.
Not too girly as still want to market to construction companies.

```html
<!DOCTYPE html>
<html lang="en">
<head>
<meta charset="utf-8">
<title>RW Office Partners – Business Card</title>
<link rel="stylesheet" href="https://fonts.googleapis.com/css2?family=Bebas+Neue&family=Montserrat:wght@500;600&family=Open+Sans:wght@400&display=swap">
<style>
  :root {
    --backdrop: #1b1b1b;
    --mauve: #986474;
    --slate: #7a8498;
    --ink: #1a1a1a;
    --paper: #ffffff;
    --card-shadow: 3px 4px 6px rgba(0,0,0,0.55);
  }
  * { margin: 0; padding: 0; box-sizing: border-box; }
  html, body { width: 1200px; height: 900px; overflow: hidden; background: var(--backdrop); }
  .stage { position: relative; width: 1200px; height: 900px; }

  .card { position: absolute; top: 200px; width: 310px; height: 502px; box-shadow: var(--card-shadow); }
  .card--front { left: 253px; background: var(--paper); border-radius: 70px 0 70px 0; }
  .card--back { left: 627px; background: var(--mauve); border-radius: 0 70px 0 70px; }

  .brand-name {
    position: absolute; top: 168px; left: 0; width: 100%;
    text-align: center;
    font-family: "Montserrat", sans-serif; font-weight: 500;
    font-size: 35px; line-height: 36px; letter-spacing: 1px;
    color: var(--slate); text-transform: uppercase;
  }

  .holder-name {
    position: absolute; top: 311px; left: 36px;
    font-family: "Montserrat", sans-serif; font-weight: 600;
    font-size: 16px; letter-spacing: 0.3px; color: var(--slate);
    text-transform: uppercase;
  }

  .contact-list, .social-list { position: absolute; left: 36px; list-style: none;
    font-family: "Open Sans", sans-serif; font-size: 13px; color: var(--ink); }
  .contact-list { top: 346px; }
  .contact-list li { display: flex; align-items: center; height: 18px; }
  .contact-list svg { width: 13px; height: 13px; margin-right: 7px; fill: var(--mauve); flex: none; }
  .contact-list .web { color: var(--mauve); }

  .social-list { top: 418px; }
  .social-list li { display: flex; align-items: center; height: 21px; }
  .social-dot { width: 17px; height: 17px; border: 1px solid var(--slate); border-radius: 50%; margin-right: 6px; flex: none; }

  .tagline {
    position: absolute; top: 98px; left: 0; width: 100%;
    text-align: center; color: var(--paper);
    font-family: "Bebas Neue", sans-serif; text-transform: uppercase;
    text-shadow: 1px 2px 3px rgba(0,0,0,0.35);
  }
  .tagline span { display: block; }
  .tagline .line-your { font-size: 124px; line-height: 112px; letter-spacing: 2px; }
  .tagline .line-organised { font-size: 64px; line-height: 62px; }
  .tagline .line-problem { font-size: 70px; line-height: 66px; }
  .tagline .line-solver { font-size: 68px; line-height: 66px; letter-spacing: 6px; }
</style>
</head>
<body>
<main class="stage">
  <section class="card card--front" aria-label="Business card front">
    <div class="brand-name">RW Office<br>Partners</div>
    <div class="holder-name">Marisol Wrenfield</div>
    <ul class="contact-list">
      <li>
        <svg viewBox="0 0 16 16" aria-hidden="true"><path d="M2 6c0-2 2-3 6-3s6 1 6 3v1h-3V5.5H5V7H2zM4 8h8l2 5H2z"/></svg>
        61 482 907 236
      </li>
      <li>
        <svg viewBox="0 0 16 16" aria-hidden="true"><path d="M1 3h14v10H1zM2.5 4.5 8 9l5.5-4.5v-.01H2.5z" fill-rule="evenodd"/></svg>
        marisol@rwofficepartners.com.au
      </li>
      <li class="web">
        <svg viewBox="0 0 16 16" aria-hidden="true"><circle cx="8" cy="8" r="7"/><path d="M3 6h10M3 10h10M8 1c-3 4-3 10 0 14M8 1c3 4 3 10 0 14" stroke="#fff" stroke-width="1" fill="none"/></svg>
        www.rwofficepartners.com.au
      </li>
    </ul>
    <ul class="social-list">
      <li><span class="social-dot" aria-hidden="true"></span>@rwofficepartners</li>
      <li><span class="social-dot" aria-hidden="true"></span>@rwofficepartners</li>
    </ul>
  </section>

  <section class="card card--back" aria-label="Business card back">
    <h1 class="tagline">
      <span class="line-your">Your</span>
      <span class="line-organised">Organised</span>
      <span class="line-problem">Problem</span>
      <span class="line-solver">Solver</span>
    </h1>
  </section>
</main>
</body>
</html>
```